Equipment Finance Specialist I work with companies who need the funds to buy their equipment

I would like a business card that stands out on the shelves. I want to be able to hand it to someone and say WOW. This card should have my logo.
You can put color into it I am very open on design and color

What my company does is we deal with dealerships that sell equipment such as Dump Trucks garbage trucks tractors trailers. Customers get referred to us and depending on their time in business we will ask for the following items

Companies that have been in business for more than two years we have a credit application program up to 250K . With this program we need the following items Credit application filled out(which is what I would like to be able for the customer to click on my website to get.) as well as three current month bank statements.

Deals over 250k we will need the following items

2 years business tax returns
2 years personal tax returns
Profit & Loss statement
Personal Financial Statement

what we do
100% FINANCING
SEASONAL PAYMENTS
LOAN BALLOON PAYMENTS
TRAC LEASING
LOW-INTEREST REFINANCING RATES
DEBT CONSOLIDATION

We specialize in creative financing solutions and offer a variety of reliable, flexible and expandable lending choices.

Target Market(s)

Trucking Companies

Industry/Entity Type

Trucking Company

Contact Information for Business Card

* $250,000 Application only Program
* Loans from $30,000 to 5,000,000
* Competitive Interest Rates

Font styles to use
Serif
Sans Serif

Colors

Designer to choose colors to be used in the design.

Requirements
Must have
• On the back of the card.
• * $250,000 Application only Program
• * Loans from $30,000 to 5,000,000
• My name, email, website. address
• * Competitive Interest Rates
• * 100% Financing
Nice to have
• I want my logo to pop on the card
• My logo is the great one I would like to use
Should not have
• I am up for your creativity as well

```html
<!DOCTYPE html>
<html lang="en">
<head>
<meta charset="utf-8">
<title>Summit Lending – Business Card</title>
<link href="https://fonts.googleapis.com/css2?family=Open+Sans:wght@400;600;700&display=swap" rel="stylesheet">
<style>
  :root {
    --navy: #1b2f7a;
    --red: #c8102e;
    --ink: #4a4a4a;
    --paper: #ffffff;
    --backdrop: #2b2b2d;
  }
  * { margin: 0; padding: 0; box-sizing: border-box; }
  html, body {
    width: 1200px;
    height: 892px;
    overflow: hidden;
    background: var(--backdrop);
    font-family: "Open Sans", Arial, sans-serif;
  }
  .card {
    position: absolute;
    width: 560px;
    height: 320px;
    background: var(--paper);
    box-shadow: 0 12px 30px rgba(0,0,0,.45);
    overflow: hidden;
  }
  .card--front { left: 70px; top: 80px; }
  .card--back { left: 570px; top: 490px; }

  /* brand name */
  .brand {
    display: flex;
    align-items: center;
    gap: 12px;
  }
  .brand__mark {
    width: 40px; height: 40px;
    border-radius: 50%;
    background: var(--red);
    flex: none;
  }
  .brand__name {
    font-weight: 700;
    font-size: 34px;
    line-height: 1;
    color: var(--navy);
    letter-spacing: .5px;
    text-transform: uppercase;
    white-space: nowrap;
  }

  /* front */
  .card--front .brand {
    position: absolute;
    left: 0; right: 0; top: 104px;
    justify-content: center;
  }
  .offer-list {
    position: absolute;
    left: 0; right: 0; top: 190px;
    text-align: center;
    color: var(--ink);
    font-size: 15px;
    line-height: 1.45;
  }
  .offer-list .sep { color: var(--navy); padding: 0 4px; }

  /* back */
  .emblem-area {
    position: absolute;
    left: 22px; top: 22px;
    width: 276px; height: 276px;
    border-radius: 50%;
    background: radial-gradient(circle at 45% 45%, #3a4f9a 0%, var(--navy) 70%);
  }
  .card--back .brand {
    position: absolute;
    right: 36px; top: 34px;
  }
  .card--back .brand__name { font-size: 26px; }
  .edge-tab {
    position: absolute;
    right: 0; top: 98px;
    width: 14px; height: 28px;
    background: var(--navy);
  }
  .person {
    position: absolute;
    right: 36px; top: 94px;
    text-align: right;
  }
  .person__name {
    font-weight: 700;
    font-size: 17px;
    color: var(--navy);
    text-transform: uppercase;
  }
  .person__role {
    font-size: 12px;
    color: var(--red);
    text-transform: uppercase;
    letter-spacing: .5px;
  }
  .contact {
    position: absolute;
    right: 36px; top: 158px;
    text-align: right;
    color: var(--ink);
    font-size: 13.5px;
    line-height: 1.5;
  }
  .contact__gap { margin-top: 8px; }
  .contact__label { color: var(--navy); font-weight: 700; }
</style>
</head>
<body>

  <section class="card card--front">
    <div class="brand">
      <span class="brand__mark"></span>
      <span class="brand__name">Summit Lending</span>
    </div>
    <p class="offer-list">
      $250,000 Application only Program<span class="sep">●</span>Loans from $30,000 to 5,000,000<br>
      Competitive Interest Rates<span class="sep">●</span>100% Financing
    </p>
  </section>

  <section class="card card--back">
    <div class="emblem-area" role="img" aria-label="Large brand emblem: navy semi-truck inside a sweeping circle"></div>
    <div class="brand">
      <span class="brand__name">Summit Lending</span>
    </div>
    <span class="edge-tab"></span>
    <div class="person">
      <p class="person__name">Mark Rowan</p>
      <p class="person__role">President</p>
    </div>
    <div class="contact">
      <p>2180 Harbor View Road</p>
      <p>Lakemont, NY 11020</p>
      <p class="contact__gap"><span class="contact__label">P:</span> 555 0142 7788</p>
      <p>mark@summitlending.com</p>
      <p>www.summitlending.com</p>
    </div>
  </section>

</body>
</html>
```